Business Card for premium dental clinic

We are a premium dental clinic based in Brasov, Romania with more than 15 year on the market, providing quality dental treatment made by a team of more specialized dentists, working with modern equipment as a solution to beautiful and healthy teeth.

Our current logo for the clinic use 2 square with colors black and gold - dr Ternisu - studio, using family fonts Bodoni, Myriad Pro and Segoe Print.
Depending on the printing we used some gold CMYK background or gold foil picture background or a gold gradient.
We want a business card:
- eye catching business card
- distinguished business card
- premium design
- to keep the color scheme of black and gold
- to attract the customers to spent time reading the information
- modern concept

```html
<!DOCTYPE html>
<html lang="en">
<head>
<meta charset="utf-8">
<title>dr Ternisu Studio – Business Card</title>
<link rel="stylesheet" href="https://fonts.googleapis.com/css2?family=Montserrat:wght@400;500;600&display=swap">
<style>
  :root {
    --stage: #1c1c1c;
    --card-dark: #232323;
    --card-light: #ffffff;
    --gold: #f2d04e;
    --gold-deep: #d9a91c;
    --ink: #2b2b2b;
    --muted: #555555;
  }
  * { box-sizing: border-box; margin: 0; padding: 0; }
  html, body {
    width: 1200px; height: 878px; overflow: hidden;
    background: var(--stage);
    font-family: "Montserrat", sans-serif;
  }
  .stage {
    position: relative; width: 1200px; height: 878px;
  }
  .card {
    position: absolute; left: 250px; width: 700px; height: 400px;
  }
  .card--back { top: 24px; background: var(--card-dark); }
  .card--front { top: 454px; background: var(--card-light); }

  .brand {
    display: flex; align-items: center; gap: 14px;
    font-weight: 500; letter-spacing: 0.02em;
  }
  .brand__square {
    width: 30px; height: 30px;
    background: linear-gradient(135deg, var(--gold), var(--gold-deep));
  }
  .card--back .brand {
    position: absolute; left: 50%; top: 50%;
    transform: translate(-50%, -50%);
    font-size: 32px; color: var(--gold);
  }
  .card--back .brand__square { width: 40px; height: 40px; }
  .card--front .brand {
    position: absolute; left: 44px; top: 40px;
    font-size: 22px; color: var(--ink);
  }

  .rule {
    position: absolute; left: 44px; right: 44px; height: 2px;
    background: var(--gold);
  }
  .rule--upper { top: 262px; right: 260px; }
  .rule--lower { top: 318px; left: 380px; }

  .holder {
    position: absolute; right: 44px; top: 268px;
    font-size: 34px; font-weight: 600; letter-spacing: 0.06em;
    color: var(--gold);
  }

  .contacts {
    position: absolute; left: 44px; top: 290px;
    list-style: none; font-size: 18px; color: var(--ink);
    letter-spacing: 0.04em; line-height: 30px;
  }
  .contacts li { display: flex; align-items: center; gap: 12px; }
  .contacts svg { width: 14px; height: 14px; flex: none; }

  .address {
    position: absolute; right: 44px; top: 332px;
    text-align: right; font-size: 18px; line-height: 26px;
    color: var(--muted); letter-spacing: 0.04em; font-style: normal;
  }
</style>
</head>
<body>
<main class="stage">
  <section class="card card--back" aria-label="Card back">
    <div class="brand"><span class="brand__square"></span>dr Ternisu Studio</div>
  </section>

  <section class="card card--front" aria-label="Card front">
    <div class="brand"><span class="brand__square"></span>dr Ternisu Studio</div>

    <div class="rule rule--upper"></div>
    <h1 class="holder">DR TERNISU</h1>
    <div class="rule rule--lower"></div>

    <ul class="contacts">
      <li>
        <svg viewBox="0 0 24 24" aria-hidden="true"><path fill="none" stroke="#f2d04e" stroke-width="2.4" d="M6 3h4l2 5-3 2a12 12 0 0 0 5 5l2-3 5 2v4a2 2 0 0 1-2 2A17 17 0 0 1 4 5a2 2 0 0 1 2-2z"/></svg>
        +40 268 555 019
      </li>
      <li>
        <svg viewBox="0 0 24 24" aria-hidden="true"><rect x="3" y="5" width="18" height="14" fill="none" stroke="#f2d04e" stroke-width="2.4"/><path d="M3 6l9 7 9-7" fill="none" stroke="#f2d04e" stroke-width="2.4"/></svg>
        info@drternisu.ro
      </li>
      <li>
        <svg viewBox="0 0 24 24" aria-hidden="true"><circle cx="12" cy="12" r="9" fill="none" stroke="#f2d04e" stroke-width="2.4"/><path d="M3 12h18M12 3c3 3 3 15 0 18M12 3c-3 3-3 15 0 18" fill="none" stroke="#f2d04e" stroke-width="1.8"/></svg>
        www.drternisu.ro
      </li>
    </ul>

    <address class="address">Strada Livezii 24,<br>Brașov 500210, Romania</address>
  </section>
</main>
</body>
</html>
```